New letter head for Air Conditioning business

We need a new professional letter head design to suit our new re-branded air conditioning business. Our new logo is attached

```html
<!DOCTYPE html>
<html lang="en">
<head>
<meta charset="utf-8">
<title>Borealis Letterhead</title>
<link rel="stylesheet" href="https://fonts.googleapis.com/css2?family=Lato:wght@300;400;700&family=Pinyon+Script&display=swap">
<style>
  :root {
    --bg: #e6e6e6;
    --paper: #f6f6f6;
    --ink: #333333;
    --ink-soft: #4a4a4a;
    --green: #5fb57f;
    --red: #e4645a;
    --brand: #3a3a3c;
  }
  * { margin: 0; padding: 0; box-sizing: border-box; }
  html, body { width: 1200px; height: 1200px; overflow: hidden; }
  body {
    background: var(--bg);
    font-family: "Lato", sans-serif;
    color: var(--ink);
    position: relative;
  }
  .letterhead {
    position: absolute;
    left: 211px;
    top: 50px;
    width: 778px;
    height: 1100px;
    background: var(--paper);
    box-shadow: 0 2px 14px rgba(0,0,0,0.12);
  }
  .brand {
    position: absolute;
    left: 59px;
    top: 52px;
    display: flex;
    align-items: center;
    gap: 10px;
  }
  .brand-dot {
    width: 18px; height: 18px; border-radius: 50%;
    background: var(--green);
  }
  .brand-name {
    font-weight: 700;
    font-size: 30px;
    letter-spacing: 2px;
    color: var(--brand);
  }
  .divider {
    position: absolute;
    top: 50px;
    width: 1px;
    height: 44px;
    background: var(--green);
  }
  .divider--contact { left: 338px; }
  .divider--address { left: 557px; }
  .contact-list, .address {
    position: absolute;
    top: 50px;
    list-style: none;
    font-size: 12.4px;
    line-height: 16px;
    color: var(--ink-soft);
  }
  .contact-list { left: 362px; }
  .contact-list li { display: flex; align-items: center; gap: 5px; }
  .contact-list svg { width: 9px; height: 9px; flex: none; }
  .address { left: 584px; }
  .letter {
    position: absolute;
    left: 83px;
    top: 260px;
    width: 612px;
    font-weight: 300;
    font-size: 12.3px;
    line-height: 18.3px;
    color: var(--ink);
  }
  .letter-date { margin-bottom: 18px; }
  .recipient-name { font-weight: 700; color: #111; }
  .recipient { margin-bottom: 28px; }
  .salutation { margin-bottom: 18px; }
  .letter-body p { text-align: justify; margin-bottom: 18.3px; }
  .closing { margin-top: 48px; }
  .signature {
    font-family: "Pinyon Script", cursive;
    font-size: 25px;
    line-height: 34px;
    color: #222;
    margin-left: 6px;
  }
  .footer-band {
    position: absolute;
    left: 0;
    bottom: 0;
    width: 778px;
    height: 15px;
    display: block;
  }
</style>
</head>
<body>
  <article class="letterhead">
    <header>
      <div class="brand">
        <span class="brand-dot"></span>
        <span class="brand-name">BOREALIS</span>
      </div>
      <span class="divider divider--contact"></span>
      <ul class="contact-list">
        <li>
          <svg viewBox="0 0 10 10"><path d="M2 1 L3.6 1 L4.2 3 L3.1 3.8 Q4 5.9 6.2 6.9 L7 5.8 L9 6.4 L9 8 Q9 9 8 9 Q1 8.3 1 2 Q1 1 2 1 Z" fill="var(--green)"/></svg>
          (+1) 410.555.0182
        </li>
        <li>
          <svg viewBox="0 0 10 10"><rect x="0.5" y="2" width="9" height="6" fill="var(--green)"/><path d="M0.5 2 L5 5.5 L9.5 2" fill="none" stroke="#fff" stroke-width="0.9"/></svg>
          hello@borealisair.com
        </li>
        <li>
          <svg viewBox="0 0 10 10"><circle cx="5" cy="5" r="4.2" fill="none" stroke="var(--green)" stroke-width="1"/><ellipse cx="5" cy="5" rx="1.8" ry="4.2" fill="none" stroke="var(--green)" stroke-width="0.8"/><line x1="0.8" y1="5" x2="9.2" y2="5" stroke="var(--green)" stroke-width="0.8"/></svg>
          www.borealisair.com
        </li>
      </ul>
      <span class="divider divider--address"></span>
      <address class="address" style="font-style: normal;">
        Unit 14, Level 2<br>
        Harbourline Ave<br>
        VIC, Australia 3100
      </address>
    </header>

    <section class="letter">
      <p class="letter-date">01 January 2050</p>
      <p class="recipient">
        <span class="recipient-name">Northgate Holdings Ltd.</span><br>
        PO Box 7120 Elmridge St<br>
        Fairview Country 7120
      </p>
      <p class="salutation">Dear Daniel Marlowe,</p>
      <div class="letter-body">
        <p>Lorem ipsum dolor sit amet, consectetuer adipiscing elit, sed diam nonummy nibh euismod tincidunt ut laoreet dolore magna aliquam erat volutpat. Ut wisi enim ad minim veniam, quis nostrud exerci tation ullamcorper suscipit lobortis nisl ut aliquip ex ea commodo consequat. Duis dolore te feugait nulla facilisi. Nam liber tempor cum soluta nobis eleifend option congue nihil imperdiet doming id quod mazim placerat facer possim assum. Lorem ipsum dolor sit amet, consectetuer adipiscing elit, sed diam nonummy nibh euismod tincidunt ut laoreet dolore magna aliquam erat volutpat. Ut wisi enim ad minim veniam, quis nostrud exerci tation ullamcorper suscipit lobortis nisl ut aliquip ex ea commodo consequat.</p>
        <p>Consectetuer adipiscing elit, sed diam nonummy nibh euismod tincidunt ut laoreet dolore magna aliquam erat volutpat. Ut wisi enim ad minim veniam, quis nostrud exerci tation ullamcorper suscipit lobortis nisl ut aliquip ex ea commodo consequat. Consectetuer adipiscing elit, sed diam nonummy nibh euismod tincidunt ut laoreet dolore magna aliquam erat volutpat. Ut wisi enim ad minim veniam, quis nostrud exerci tation ullamcorper suscipit lobortis nisl ut aliquip ex ea commodo consequat.</p>
        <p>Consectetuer adipiscing elit, sed diam nonummy nibh euismod tincidunt ut laoreet dolore magna aliquam erat volutpat. Ut wisi enim ad minim veniam, quis nostrud exerci tation ullamcorper suscipit lobortis nisl ut aliquip ex ea commodo consequat. Consectetuer adipiscing elit, sed diam nonummy nibh euismod tincidunt ut laoreet dolore magna aliquam erat volutpat. Ut wisi enim ad minim veniam, quis nostrud exerci tation ullamcorper suscipit lobortis nisl ut aliquip ex ea commodo consequat.</p>
      </div>
      <p class="closing">Sincerely Yours</p>
      <p class="signature">Thomas Evan Carroway</p>
    </section>

    <svg class="footer-band" viewBox="0 0 778 15" preserveAspectRatio="none" aria-hidden="true">
      <polygon points="0,0 389,0 381,15 0,15" fill="var(--green)"/>
      <polygon points="394,0 778,0 778,15 386,15" fill="var(--red)"/>
    </svg>
  </article>
</body>
</html>
```